Modern Verdell Tree Care Website

I need a website for a full service Tree Care company. The company provides tree pruning, tree removal, tree preservation, emergency services, stump grinding, and emergency tree services.

Target Market(s)

Customers that need tree services

Industry/Entity Type

Landscaping, Tree Services

Coding

Coded - Design and coding required

Number of Pages Required

5+ page

Font styles to use
Sans Serif

Requirements
Must have
• Good clean design that showcases the services the company provides.
Nice to have
• Services page; contact form, blog, home page, about page

```html
<!DOCTYPE html>
<html lang="en">
<head>
<meta charset="utf-8">
<title>Verdell Tree Care</title>
<link href="https://fonts.googleapis.com/css2?family=Open+Sans:wght@400;600;700;800&family=Lato:wght@400;700&display=swap" rel="stylesheet">
<style>
:root{
  --green:#8cc63f;
  --green-dark:#79b22f;
  --navy:#1c1a4a;
  --ink:#1f2140;
  --text:#8b8fa3;
  --blue:#1f6fd1;
  --orange:#f1a935;
  --footer:#1d1638;
  --light:#f1f4f8;
  --white:#ffffff;
}
*{margin:0;padding:0;box-sizing:border-box}
html,body{width:1200px;height:4486px;overflow:hidden}
body{position:relative;background:var(--white);font-family:"Lato",sans-serif;color:var(--text)}
.abs{position:absolute}
h1,h2,h3,h4{font-family:"Open Sans",sans-serif;color:var(--navy)}

/* header */
.topbar{left:819px;top:0;width:247px;height:30px;background:var(--blue);clip-path:polygon(6% 0,100% 0,94% 100%,0 100%);display:flex;align-items:center;justify-content:space-around;font-size:13px;color:#fff;font-weight:700;padding:0 18px}
.topbar .login{background:#2aa6d8;padding:2px 12px;border-radius:2px}
.brand{display:flex;align-items:center;gap:12px;font-family:"Open Sans",sans-serif;font-weight:800;font-size:24px;color:var(--navy)}
.brand-mark{width:40px;height:40px;background:var(--green)}
.nav{top:48px;font-size:14px;color:var(--ink);font-family:"Lato",sans-serif}

/* hero */
.hero{left:0;top:87px;width:1200px;height:726px;background:linear-gradient(160deg,#4d5f3c 0%,#6b7b50 40%,#3f4a30 100%)}
.welcome{left:531px;top:298px;width:162px;height:38px;background:var(--green);color:#fff;font-size:12px;font-weight:700;display:flex;align-items:center;justify-content:center;border-radius:3px;font-family:"Open Sans",sans-serif}
.hero-title{left:0;width:1200px;top:350px;text-align:center;color:#fff;font-size:58px;line-height:72px;font-weight:700}
.outline-btn{left:528px;top:517px;width:167px;height:47px;border:1.5px solid #fff;color:#fff;font-size:12px;font-weight:700;display:flex;align-items:center;justify-content:center;border-radius:3px;font-family:"Open Sans",sans-serif}
.curve{left:0;width:1200px}

/* about */
.photo{background:linear-gradient(150deg,#6f8a4a,#3d4f2c)}
.eyebrow{font-size:12px;color:var(--green);font-weight:700;font-family:"Open Sans",sans-serif;text-decoration:underline;text-underline-offset:3px}
.about-title{left:620px;top:952px;font-size:37px;line-height:48px;font-weight:700}
.about-sub{left:620px;top:1070px;font-size:19px;color:var(--ink);font-family:"Open Sans",sans-serif}
.para{font-size:12px;line-height:19px;color:var(--text)}
.green-btn{background:var(--green);color:#fff;font-size:14px;font-weight:700;display:flex;align-items:center;justify-content:center;gap:10px;border-radius:2px;font-family:"Open Sans",sans-serif}

/* services */
.services-bg{left:0;top:1516px;width:1200px;height:574px;background:var(--light)}
.center-label{left:0;width:1200px;text-align:center}
.section-title{font-size:40px;font-weight:700;text-align:center;left:0;width:1200px}
.service-card{top:1784px;width:304px;height:212px;background:#fff;box-shadow:0 4px 14px rgba(30,30,80,.07);text-align:center}
.service-photo{position:absolute;left:79px;top:-73px;width:146px;height:146px;border-radius:50%;border:6px solid #fff;box-shadow:0 4px 10px rgba(0,0,0,.1)}
.badge{position:absolute;left:138px;top:66px;width:28px;height:28px;border-radius:50%;background:var(--green);color:#fff;font-size:11px;font-weight:700;display:flex;align-items:center;justify-content:center;border:2px solid #fff}
.service-card h3{position:absolute;top:112px;width:100%;font-size:17px;font-weight:700}
.service-card p{position:absolute;top:138px;left:38px;width:228px;font-size:12px;line-height:19px}

/* features band */
.feature-photo{left:0;top:2090px;width:1200px;height:589px;background:linear-gradient(180deg,#5b7a3a 0%,#8aa65a 50%,#7c9a48 100%)}
.panel{left:0;width:1200px}
.panel h4{position:absolute;left:807px;font-size:21px;font-weight:700;color:#fff;letter-spacing:.3px}
.panel p{position:absolute;left:807px;width:280px;font-size:12.5px;line-height:21px;color:rgba(255,255,255,.85)}

/* faq */
.faq-title{left:610px;top:2786px;font-size:36px;font-weight:700}
.acc{left:610px;width:473px;font-size:13px;font-weight:700;font-family:"Open Sans",sans-serif;display:flex;align-items:center;padding-left:26px}
.acc-open{top:2857px;height:56px;background:var(--green);color:#fff}
.acc-closed{height:56px;background:var(--light);color:var(--navy)}
.acc .toggle{position:absolute;right:14px;width:28px;height:28px;background:#fff;color:var(--navy);display:flex;align-items:center;justify-content:center;font-size:14px}
.acc-body{left:636px;top:2943px;width:430px;font-size:13px;line-height:29px;color:#555a70}

/* testimonials */
.testi-bg{left:0;top:3336px;width:1200px;height:557px;background:#f7f8fb}
.testi{top:3557px;width:304px;height:173px;background:#fff;padding:20px 22px;font-size:16px;line-height:23px;color:#4b4f66;box-shadow:0 3px 12px rgba(30,30,80,.05)}
.testi.active{background:var(--green);color:#fff}
.tail{top:3730px;width:0;height:0;border-left:18px solid var(--green);border-bottom:18px solid transparent}
.avatar{width:52px;height:52px;border-radius:50%;background:linear-gradient(160deg,#c9ccd6,#8b8fa3);border:3px solid #fff}
.person{font-size:14px;color:var(--navy);font-weight:700;font-family:"Open Sans",sans-serif}
.role{font-size:12px;color:#a4a8b8}
.dot{top:3855px;width:8px;height:8px;border-radius:50%;background:var(--green)}

/* footer */
.footer{left:0;top:3893px;width:1200px;height:593px;background:var(--footer)}
.foot-brand{left:127px;top:4060px;font-family:"Open Sans",sans-serif;font-weight:800;font-size:30px;color:#fff;display:flex;align-items:center;gap:14px}
.foot-brand .brand-mark{width:44px;height:44px;background:#fff}
.foot-text{font-size:12px;line-height:21px;color:#b5b2c9}
.social{top:4226px;width:30px;height:30px;background:#2e2750;border-radius:2px}
.social.on{background:var(--green)}
.foot-head{font-size:15px;font-weight:700;color:#fff;font-family:"Open Sans",sans-serif}
.foot-links{font-size:11.5px;line-height:26px;color:#b5b2c9;list-style:none}
.email-input{left:827px;top:4170px;width:194px;height:46px;background:#fff;font-size:12px;color:#8b8fa3;display:flex;align-items:center;padding-left:24px}
.email-btn{left:1021px;top:4170px;width:49px;height:46px;background:var(--green);display:flex;align-items:center;justify-content:center}
.contact-icon{top:4325px;width:46px;height:46px;border-radius:50%;background:#352d5c;display:flex;align-items:center;justify-content:center}
.contact-icon.on{background:var(--green)}
.contact-title{top:4328px;font-size:15px;font-weight:700;color:#fff;font-family:"Open Sans",sans-serif}
.contact-line{top:4350px;font-size:12px;color:#b5b2c9}
.divider{left:110px;top:4435px;width:980px;height:1px;background:#352d5c}
.copy{left:0;width:1200px;top:4454px;text-align:center;font-size:12px;color:#fff}
</style>
</head>
<body>

<!-- header -->
<div class="abs topbar"><span class="login">Log in</span><span>+1 (555) 013-2740</span></div>
<div class="abs brand" style="left:110px;top:24px"><span class="brand-mark"></span>Verdell Tree Care</div>
<span class="abs nav" style="left:519px">Home</span>
<span class="abs nav" style="left:611px">About Us</span>
<span class="abs nav" style="left:707px">Services</span>
<span class="abs nav" style="left:806px">Giving Back</span>
<span class="abs nav" style="left:918px">And more</span>
<span class="abs nav" style="left:1015px">Login</span>

<!-- hero -->
<div class="abs hero" role="img" aria-label="Arborist in harness climbing and cutting a large tree trunk"></div>
<div class="abs welcome">WELCOME</div>
<h1 class="abs hero-title">We Offer Sustainable<br>Tree Solutions</h1>
<div class="abs outline-btn">ABOUT COMPANY</div>
<svg class="abs curve" style="top:700px" width="1200" height="114" viewBox="0 700 1200 114">
  <path d="M0 813 L0 790 Q600 680 1200 790 L1200 813 Z" fill="#fff"/>
  <path d="M110 796 Q600 702 1090 796 Q600 722 110 796 Z" fill="#8cc63f"/>
</svg>

<!-- about -->
<div class="abs photo" style="left:145px;top:963px;width:174px;height:218px" role="img" aria-label="Climber pruning branches with a chainsaw"></div>
<div class="abs photo" style="left:341px;top:880px;width:232px;height:301px;background:linear-gradient(150deg,#5a5f4a,#2f3a25)" role="img" aria-label="Crew feeding branches into a wood chipper"></div>
<div class="abs photo" style="left:197px;top:1197px;width:139px;height:139px" role="img" aria-label="Arborist working high in a tree canopy"></div>
<div class="abs photo" style="left:359px;top:1197px;width:184px;height:169px;background:linear-gradient(160deg,#b9c4cc,#6f7a63)" role="img" aria-label="Arborist in blue climbing bare tree limbs"></div>
<span class="abs eyebrow" style="left:620px;top:921px">WHO WE ARE</span>
<h2 class="abs about-title">Your Partner in Tree<br>Presevation</h2>
<p class="abs about-sub">Enhancing Landscapes, One Tree at a Time</p>
<p class="abs para" style="left:620px;top:1109px;width:455px">Lorem ipsum dolor sit amet, consectetur adipiscing elit, sed do eiusmod temp or incididunt ut labore et dolore magna aliqua. Ut enim ad minim veniam, quis laboris nisi ut aliquip ex ea commodo consequat.</p>
<p class="abs para" style="left:620px;top:1177px;width:455px">Lorem ipsum dolor sit amet, consectetur adipiscing elit, sed do eiusmod temp or incididunt ut labore et dolore magna aliqua.</p>
<div class="abs green-btn" style="left:620px;top:1242px;width:136px;height:40px">Contact us
  <svg width="16" height="12" viewBox="0 0 16 12"><path d="M1 6h13M9 1l5 5-5 5" stroke="#fff" stroke-width="1.6" fill="none"/></svg>
</div>

<!-- services -->
<div class="abs services-bg"></div>
<svg class="abs curve" style="top:1460px" width="1200" height="60" viewBox="0 1460 1200 60">
  <path d="M0 1518 L0 1512 Q600 1408 1200 1512 L1200 1518 Z" fill="#f1f4f8"/>
  <path d="M110 1516 Q600 1420 1090 1516 Q600 1440 110 1516 Z" fill="#8cc63f"/>
</svg>
<span class="abs eyebrow center-label" style="top:1569px">OUR SERVICES</span>
<h2 class="abs section-title" style="top:1602px">Services We Provide</h2>

<div class="abs service-card" style="left:120px">
  <div class="service-photo photo" role="img" aria-label="Worker pruning a small tree"></div>
  <div class="badge">01</div>
  <h3>Tree Pruning</h3>
  <p>Lorem ipsum dolor sit amet, consect etur adipiscing elit, sed do eiu smod tempor</p>
</div>
<div class="abs service-card" style="left:448px">
  <div class="service-photo photo" style="background:linear-gradient(150deg,#9a8a5a,#4d5a2c)" role="img" aria-label="Freshly cut tree stump on grass"></div>
  <div class="badge">02</div>
  <h3>Tree Removal</h3>
  <p>Lorem ipsum dolor sit amet, consect etur adipiscing elit, sed do eiu smod tempor</p>
</div>
<div class="abs service-card" style="left:775px">
  <div class="service-photo photo" style="background:linear-gradient(150deg,#8fb36a,#3f6a2e)" role="img" aria-label="Two people resting by a row of trimmed hedges"></div>
  <div class="badge">03</div>
  <h3>Stump Grinding</h3>
  <p>Lorem ipsum dolor sit amet, consect etur adipiscing elit, sed do eiu smod tempor</p>
</div>

<!-- features band -->
<div class="abs feature-photo" role="img" aria-label="Leafy trees over a lawn and winding garden path"></div>
<svg class="abs panel" style="top:2090px" width="1200" height="589" viewBox="0 0 1200 589">
  <polygon points="787,0 1200,0 1200,206 755,206" fill="#f1a935" opacity=".93"/>
  <polygon points="745,206 1200,206 1200,410 714,410" fill="#2a2c3a" opacity=".93"/>
  <polygon points="709,410 1200,410 1200,589 676,589" fill="#8cc63f" opacity=".93"/>
</svg>
<div class="abs panel" style="top:2090px;height:589px">
  <h4 style="top:74px">PROFESSIONALISM</h4>
  <p style="top:110px">Lorem ipsum dolor sit amet, consectetur ad ipiscing elit, sed do eiusmod tempor</p>
  <h4 style="top:270px">PROVEN RECORD</h4>
  <p style="top:306px">Lorem ipsum dolor sit amet, consectetur ad ipiscing elit, sed do eiusmod tempor</p>
  <h4 style="top:474px">CLIENT-CENTRIC</h4>
  <p style="top:510px">Lorem ipsum dolor sit amet, consectetur ad ipiscing elit, sed do eiusmod tempor</p>
</div>

<!-- faq -->
<svg class="abs" style="left:120px;top:2790px" width="400" height="400" viewBox="0 0 400 400">
  <circle cx="188" cy="190" r="178" fill="#8cc63f"/>
  <circle cx="222" cy="218" r="178" fill="#1c1a4a"/>
</svg>
<div class="abs" style="left:154px;top:2826px;width:336px;height:336px;border-radius:50%;background:linear-gradient(160deg,#5e8fd6,#3a6fc0 55%,#6d6a4a)" role="img" aria-label="Arborist cutting a trunk section against blue sky"></div>
<span class="abs eyebrow" style="left:610px;top:2753px">FAQS</span>
<h2 class="abs faq-title">Frequently Asked Questions</h2>
<div class="abs acc acc-open">How to Get Started with our Programs<span class="toggle">&minus;</span></div>
<p class="abs acc-body">Lorem ipsum dolor sit amet, consectetur adipiscing elit, sed do eiusmod tempor incididunt ut labore et dolore magna aliqua. Ut enim ad minim veniam, enim ad minim veniam,</p>
<div class="abs acc acc-closed" style="top:3054px">How to Get Started with our Programs<span class="toggle">+</span></div>
<div class="abs acc acc-closed" style="top:3120px">How to Get Started with our Programs<span class="toggle">+</span></div>

<!-- testimonials -->
<div class="abs testi-bg"></div>
<svg class="abs curve" style="top:3270px" width="1200" height="70" viewBox="0 3270 1200 70">
  <path d="M0 3270 L1200 3270 L1200 3284 Q600 3380 0 3284 Z" fill="#fff"/>
  <path d="M110 3284 Q600 3384 1090 3284 Q600 3362 110 3284 Z" fill="#8cc63f"/>
</svg>
<span class="abs eyebrow center-label" style="top:3421px">TESTIMONIALS</span>
<h2 class="abs section-title" style="top:3456px">What Clients are Saying</h2>

<div class="abs testi" style="left:120px">Lorem ipsum dolor sit amet, consectetur adipiscing elit, sed d o eiusmod tempor incididunt ut lab ore et dolore magna aliqua. Ut enim ad min</div>
<div class="abs testi active" style="left:448px">Lorem ipsum dolor sit amet, consectetur adipiscing elit, sed d o eiusmod tempor incididunt ut lab ore et dolore magna aliqua. Ut enim ad min</div>
<div class="abs testi" style="left:778px">Lorem ipsum dolor sit amet, consectetur adipiscing elit, sed d o eiusmod tempor incididunt ut lab ore et dolore magna aliqua. Ut enim ad min</div>
<div class="abs tail" style="left:120px"></div>
<div class="abs tail" style="left:448px"></div>
<div class="abs tail" style="left:778px"></div>

<div class="abs avatar" style="left:139px;top:3756px" role="img" aria-label="Client portrait"></div>
<span class="abs person" style="left:213px;top:3756px">Dana Reyes</span>
<span class="abs role" style="left:213px;top:3779px">Engineer</span>
<div class="abs avatar" style="left:467px;top:3756px" role="img" aria-label="Client portrait"></div>
<span class="abs person" style="left:541px;top:3756px">Mark Ellison</span>
<span class="abs role" style="left:541px;top:3779px">Engineer</span>
<div class="abs avatar" style="left:797px;top:3756px" role="img" aria-label="Client portrait"></div>
<span class="abs person" style="left:871px;top:3756px">Nora Quill</span>
<span class="abs role" style="left:871px;top:3779px">Engineer</span>

<div class="abs dot" style="left:571px;width:20px;border-radius:4px"></div>
<div class="abs dot" style="left:598px"></div>
<div class="abs dot" style="left:611px"></div>
<div class="abs dot" style="left:624px"></div>

<!-- footer -->
<div class="abs footer"></div>
<svg class="abs curve" style="top:3890px" width="1200" height="100" viewBox="0 3890 1200 100">
  <path d="M0 3890 L1200 3890 L1200 3893 Q600 4000 0 3893 Z" fill="#f7f8fb"/>
  <path d="M110 3911 Q600 4028 1090 3911 Q600 4002 110 3911 Z" fill="#8cc63f"/>
</svg>

<div class="abs foot-brand"><span class="brand-mark"></span>Verdell Tree Care</div>
<p class="abs foot-text" style="left:127px;top:4148px;width:290px">Lorem ipsum dolor sit amet, consectetur adipiscing elit, sed do eiusmod tempor incididunt ut</p>
<div class="abs social on" style="left:127px"></div>
<div class="abs social" style="left:165px"></div>
<div class="abs social" style="left:204px"></div>
<div class="abs social" style="left:242px"></div>

<h4 class="abs foot-head" style="left:491px;top:4070px">Quick Links</h4>
<ul class="abs foot-links" style="left:491px;top:4110px">
  <li>Lorest Services</li><li>Lorest Services</li><li>Lorest Services</li><li>Lorest Services</li><li>Lorest Services</li><li>Lorest Services</li>
</ul>
<ul class="abs foot-links" style="left:625px;top:4110px">
  <li>Lorest Services</li><li>Lorest Services</li><li>Lorest Services</li><li>Lorest Services</li><li>Lorest Services</li>
</ul>

<h4 class="abs foot-head" style="left:827px;top:4070px">Newsletters</h4>
<p class="abs foot-text" style="left:827px;top:4112px;width:250px;font-size:11.5px">Lorem ipsum dolor sit amet, consectetur adi piscing elit, sed do eiusmod tempor</p>
<div class="abs email-input">Enter Email Address</div>
<div class="abs email-btn"><svg width="14" height="18" viewBox="0 0 14 18"><path d="M3 2l8 7-8 7" stroke="#fff" stroke-width="2.4" fill="none"/></svg></div>

<div class="abs contact-icon" style="left:127px"><svg width="16" height="20" viewBox="0 0 16 20"><path d="M8 1a6 6 0 0 0-6 6c0 5 6 12 6 12s6-7 6-12a6 6 0 0 0-6-6z" fill="#6c6494"/><circle cx="8" cy="7" r="2.2" fill="#352d5c"/></svg></div>
<span class="abs contact-title" style="left:190px">Address</span>
<span class="abs contact-line" style="left:190px">48 Alder Lane</span>

<div class="abs contact-icon on" style="left:365px"><svg width="20" height="14" viewBox="0 0 20 14"><rect x="1" y="1" width="18" height="12" rx="1" fill="#fff"/><path d="M1 1l9 7 9-7" stroke="#8cc63f" stroke-width="1.5" fill="none"/></svg></div>
<span class="abs contact-title" style="left:430px">Email Us</span>
<span class="abs contact-line" style="left:430px">hello@verdelltree.example</span>

<div class="abs contact-icon" style="left:632px"><svg width="18" height="18" viewBox="0 0 18 18"><path d="M4 1l3 4-2 2c1 2 3 4 5 5l2-2 4 3-2 3C8 16 2 10 1 4z" fill="#6c6494"/></svg></div>
<span class="abs contact-title" style="left:697px">Contact Us</span>
<span class="abs contact-line" style="left:697px">+1 (555) 014-8821</span>

<div class="abs contact-icon" style="left:862px"><svg width="20" height="20" viewBox="0 0 20 20"><circle cx="10" cy="10" r="8" stroke="#6c6494" stroke-width="2" fill="none"/><path d="M10 5v5l3 2" stroke="#6c6494" stroke-width="2" fill="none"/></svg></div>
<span class="abs contact-title" style="left:923px">Opening Hour</span>
<span class="abs contact-line" style="left:923px">Mon - Friday 10 am - 8pm</span>

<div class="abs divider"></div>
<p class="abs copy">Verdell Tree Care</p>

</body>
</html>
```